SOLVE Study flyer

I need help designing a flyer for a research study that will include brain imaging in adolescents. The info is in the attached document. The study is called the Sequoia Outlook Lantern Valley Echo (SOLVE) study. Ideally this would be returned as a document that I can edit in the future as we will have several new recruitment phases (different age groups, etc. I also would love to have a logo designed as part of this project, but I recognize that might be a separate design request.

```html
<!DOCTYPE html>
<html lang="en">
<head>
<meta charset="utf-8">
<title>SOLVE Study – Recruitment Flyer</title>
<link rel="stylesheet" href="https://fonts.googleapis.com/css2?family=Montserrat:wght@700&family=Asap+Condensed:ital,wght@1,600&family=Lato:ital,wght@0,400;0,700;1,700&display=swap">
<style>
  :root {
    --purple: #4b2c83;
    --purple-deep: #3f2570;
    --teal: #38c5d0;
    --ink: #3a3a3a;
    --white: #ffffff;
    --paper: #ffffff;
  }
  * { margin: 0; padding: 0; box-sizing: border-box; }
  html, body { width: 927px; height: 1200px; overflow: hidden; background: var(--paper); }
  .flyer { position: relative; width: 927px; height: 1200px; overflow: hidden; font-family: "Lato", sans-serif; color: var(--ink); }

  .hero-backdrop {
    position: absolute; left: 0; top: 0; width: 927px; height: 640px;
    background: linear-gradient(180deg, #eef0ea 0%, #f1ede9 45%, #f6f4f3 75%, rgba(255,255,255,0) 100%);
  }

  .photo { position: absolute; border-radius: 50%; box-shadow: 0 2px 6px rgba(0,0,0,0.08); }
  .photo--friends-hallway { left: 517px; top: 30px; width: 390px; height: 302px; background: radial-gradient(ellipse at 60% 45%, #a9825f 0%, #6d5444 45%, #3e3332 100%); }
  .photo--friends-trio { left: 38px; top: 423px; width: 390px; height: 302px; background: radial-gradient(ellipse at 50% 55%, #c49a7e 0%, #8e6a51 45%, #4a3a2e 100%); }
  .photo--girl-journal { left: 486px; top: 728px; width: 390px; height: 302px; background: radial-gradient(ellipse at 50% 55%, #efe6dc 0%, #d8c6b3 50%, #b59e88 100%); }

  .title { position: absolute; left: 34px; top: 22px; font-family: "Montserrat", sans-serif; font-weight: 700; font-size: 60px; letter-spacing: -0.5px; line-height: 1; }
  .title__name { color: var(--purple); }
  .title__word { color: var(--teal); }

  .subtitle { position: absolute; left: 34px; top: 114px; font-family: "Asap Condensed", sans-serif; font-style: italic; font-weight: 600; font-size: 25px; line-height: 38px; color: var(--purple); }

  .brush { position: absolute; }
  .brush svg { position: absolute; inset: 0; width: 100%; height: 100%; }
  .brush__text { position: relative; color: var(--white); }

  .brush--question { left: 12px; top: 210px; width: 445px; height: 88px; }
  .brush--question .brush__text { padding: 17px 0 0 33px; font-size: 18.5px; line-height: 29px; }

  .intro { position: absolute; left: 38px; top: 345px; width: 860px; font-style: italic; font-weight: 700; font-size: 17.6px; line-height: 26px; color: var(--purple); }

  .brush--involves { left: 470px; top: 431px; width: 282px; height: 50px; }
  .brush--involves .brush__text { padding: 11px 0 0 22px; font-weight: 700; font-size: 18.5px; }

  .brush--eligible { left: 40px; top: 774px; width: 310px; height: 50px; }
  .brush--eligible .brush__text { padding: 11px 0 0 22px; font-weight: 700; font-size: 18.5px; }

  .list { position: absolute; list-style: none; font-size: 16.5px; line-height: 25.5px; color: var(--ink); }
  .list li { position: relative; padding-left: 32px; }
  .list li svg { position: absolute; left: 0; top: 5px; width: 15px; height: 15px; }
  .list--involves { left: 482px; top: 497px; width: 400px; }
  .list--involves li + li { margin-top: 13px; }
  .list--eligible { left: 52px; top: 840px; width: 400px; }
  .list--eligible li + li { margin-top: 13px; }

  .brush--compensation { left: 12px; top: 1014px; width: 368px; height: 140px; }
  .compensation__icon { position: absolute; left: 48px; top: 1060px; width: 54px; height: 54px; }
  .compensation__label { position: absolute; left: 131px; top: 1037px; font-weight: 700; font-size: 25px; color: var(--white); }
  .compensation__amount { position: absolute; left: 134px; top: 1072px; font-weight: 700; font-size: 60px; letter-spacing: -1px; color: var(--white); }

  .contact-band { position: absolute; left: 0; top: 1050px; width: 927px; height: 150px; }
  .contact__invite { position: absolute; left: 461px; top: 1080px; width: 430px; font-size: 16.2px; line-height: 25px; color: var(--white); }
  .contact__mail-icon { position: absolute; left: 464px; top: 1150px; width: 31px; height: 22px; }
  .contact__email { position: absolute; left: 512px; top: 1145px; font-weight: 700; font-size: 24px; color: var(--white); }
</style>
</head>
<body>
<main class="flyer">
  <div class="hero-backdrop" role="img" aria-label="Faded background photo of smiling girls walking together outdoors"></div>

  <h1 class="title"><span class="title__name">SOLVE</span> <span class="title__word">Study</span></h1>
  <p class="subtitle">Sequoia Outlook Lantern<br>Valley Echo</p>

  <div class="brush brush--question">
    <svg viewBox="0 0 445 88" preserveAspectRatio="none" aria-hidden="true"><path fill="var(--purple)" d="M8 10 L60 6 L64 2 L200 4 L230 0 L238 3 L420 5 L438 6 L443 18 L440 30 L445 46 L440 60 L443 78 L430 84 L300 86 L170 85 L60 88 L12 84 L4 70 L0 50 L6 30 L2 18 Z"/></svg>
    <p class="brush__text">Are you the parent of a child age 10-17? Do they<br>worry or overthink negative emotions?</p>
  </div>

  <div class="photo photo--friends-hallway" role="img" aria-label="Photo of two teenage girls laughing together in a school hallway"></div>

  <p class="intro">Lantern Valley University researchers are seeking girls age 10-17 for a study about brain activity in emotions and decision-making and how they relate to puberty, anxiety and depression.</p>

  <div class="photo photo--friends-trio" role="img" aria-label="Photo of three smiling teenage girls posing together outdoors"></div>

  <div class="brush brush--involves">
    <svg viewBox="0 0 282 50" preserveAspectRatio="none" aria-hidden="true"><path fill="var(--purple)" d="M6 6 L110 4 L116 0 L150 2 L270 3 L276 8 L280 20 L277 34 L280 44 L260 48 L140 47 L20 50 L4 44 L0 28 L3 14 Z"/></svg>
    <h2 class="brush__text">Study participation involves</h2>
  </div>

  <ul class="list list--involves">
    <li><svg viewBox="0 0 16 16" aria-hidden="true"><defs><linearGradient id="bulletA" x1="0" y1="0" x2="0" y2="1"><stop offset="0" stop-color="#3aa7d6"/><stop offset="1" stop-color="#4b2c83"/></linearGradient></defs><circle cx="8" cy="8" r="8" fill="url(#bulletA)"/><path d="M4 8 H11 M8.5 5.5 L11 8 L8.5 10.5" stroke="#fff" stroke-width="1.5" fill="none" stroke-linecap="round" stroke-linejoin="round"/></svg>One one-hour interview (online or in-person) where your child will discuss their thoughts</li>
    <li><svg viewBox="0 0 16 16" aria-hidden="true"><circle cx="8" cy="8" r="8" fill="url(#bulletA)"/><path d="M4 8 H11 M8.5 5.5 L11 8 L8.5 10.5" stroke="#fff" stroke-width="1.5" fill="none" stroke-linecap="round" stroke-linejoin="round"/></svg>Online questionnaires (parent and child)</li>
    <li><svg viewBox="0 0 16 16" aria-hidden="true"><circle cx="8" cy="8" r="8" fill="url(#bulletA)"/><path d="M4 8 H11 M8.5 5.5 L11 8 L8.5 10.5" stroke="#fff" stroke-width="1.5" fill="none" stroke-linecap="round" stroke-linejoin="round"/></svg>One two-hour visit where your child will complete an MRI scan, answer questions about their puberty stage, and have a small hair sample taken to study puberty hormones</li>
  </ul>

  <div class="photo photo--girl-journal" role="img" aria-label="Photo of a thoughtful teenage girl lying on her bed with a notebook"></div>

  <div class="brush brush--eligible">
    <svg viewBox="0 0 310 50" preserveAspectRatio="none" aria-hidden="true"><path fill="var(--purple)" d="M6 6 L108 4 L112 0 L150 2 L298 4 L304 10 L308 22 L305 34 L309 46 L280 48 L150 47 L18 50 L4 44 L0 28 L3 14 Z"/></svg>
    <h2 class="brush__text">Your child may be eligible if they</h2>
  </div>

  <ul class="list list--eligible">
    <li><svg viewBox="0 0 16 16" aria-hidden="true"><circle cx="8" cy="8" r="8" fill="url(#bulletA)"/><path d="M4 8 H11 M8.5 5.5 L11 8 L8.5 10.5" stroke="#fff" stroke-width="1.5" fill="none" stroke-linecap="round" stroke-linejoin="round"/></svg>Are age 10-17</li>
    <li><svg viewBox="0 0 16 16" aria-hidden="true"><circle cx="8" cy="8" r="8" fill="url(#bulletA)"/><path d="M4 8 H11 M8.5 5.5 L11 8 L8.5 10.5" stroke="#fff" stroke-width="1.5" fill="none" stroke-linecap="round" stroke-linejoin="round"/></svg>Tend to worry or overthink negative thoughts</li>
    <li><svg viewBox="0 0 16 16" aria-hidden="true"><circle cx="8" cy="8" r="8" fill="url(#bulletA)"/><path d="M4 8 H11 M8.5 5.5 L11 8 L8.5 10.5" stroke="#fff" stroke-width="1.5" fill="none" stroke-linecap="round" stroke-linejoin="round"/></svg>have not been diagnosed with psychosis, learning problems, or autism</li>
  </ul>

  <div class="brush brush--compensation">
    <svg viewBox="0 0 368 140" preserveAspectRatio="none" aria-hidden="true"><path fill="var(--teal)" d="M10 14 L70 8 L90 2 L200 6 L250 4 L355 10 L362 20 L358 40 L366 60 L360 90 L366 120 L356 132 L250 134 L150 138 L60 136 L14 132 L4 110 L0 80 L6 50 L2 28 Z"/></svg>
  </div>
  <svg class="compensation__icon" viewBox="0 0 54 54" aria-hidden="true">
    <path d="M20 6 L34 6 L30 12 L24 12 Z" fill="#fff"/>
    <ellipse cx="27" cy="25" rx="14" ry="13" fill="#fff"/>
    <text x="27" y="31" text-anchor="middle" font-family="Lato, sans-serif" font-weight="700" font-size="16" fill="var(--teal)">$</text>
    <rect x="1" y="37" width="7" height="12" fill="#fff"/>
    <path d="M10 40 L22 38 L32 41 L46 36 Q52 35 50 40 L36 48 L12 48 Z" fill="#fff"/>
  </svg>
  <p class="compensation__label">Compensation up to</p>
  <p class="compensation__amount">$140</p>

  <svg class="contact-band" viewBox="0 0 927 150" preserveAspectRatio="none" aria-hidden="true">
    <polygon points="442,0 927,0 927,150 387,150" fill="var(--purple)"/>
    <rect x="0" y="139" width="927" height="11" fill="var(--purple)"/>
  </svg>
  <p class="contact__invite">Interested in participating? Want more information? Please contact us!</p>
  <svg class="contact__mail-icon" viewBox="0 0 31 22" aria-hidden="true">
    <rect x="1" y="1" width="29" height="20" fill="none" stroke="#fff" stroke-width="2"/>
    <path d="M1 1 L15.5 13 L30 1 M1 21 L12 10 M30 21 L19 10" fill="none" stroke="#fff" stroke-width="2"/>
  </svg>
  <p class="contact__email">solvestudy@lanternvalley.edu</p>
</main>
</body>
</html>
```